Emerging Ed-Tech Startup seeking Stationery Designs!

We are in need of basic set of stationery designs to be used for our business operations, letters, emails, and in-office materials. We are a technology startup enhancing on campus work experience offerings by establishing a collaborative work environment for the completion of such tasks.

Our colors are Vibrant Tiffany Blue/Black/White.

Website: www.campusnorthway.com (Still under construction aside from the landing pages)

Please make sure the designs use a brighter more vibrant tiffany blue color than seen in the image files uploaded. We are not using those materials.

Our logo has been added as a file as well, please use that for any designs (include that logo). Thank you.

```html
<!DOCTYPE html>
<html lang="en">
<head>
<meta charset="utf-8">
<title>Campus Northway Stationery</title>
<link rel="stylesheet" href="https://fonts.googleapis.com/css2?family=Oswald:wght@600&family=Roboto:wght@400;500&family=Roboto+Condensed:wght@400&display=swap">
<style>
  :root {
    --tiffany: #0ce8ea;
    --tiffany-soft: #bff7f8;
    --black: #0c0c0c;
    --white: #ffffff;
    --ink: #222222;
    --rule: #333333;
    --stage: #e9e6e1;
    --faint: #ececec;
  }
  * { box-sizing: border-box; margin: 0; padding: 0; }
  html, body { width: 1200px; height: 696px; overflow: hidden; }
  body {
    position: relative;
    background: var(--stage);
    font-family: "Roboto", Arial, sans-serif;
    color: var(--ink);
  }
  .sheet {
    position: absolute;
    background: var(--white);
    border: 1px solid #9a9a9a;
    overflow: hidden;
  }
  .wordmark {
    font-family: "Oswald", "Arial Narrow", sans-serif;
    font-weight: 600;
    color: var(--black);
    line-height: 0.95;
    letter-spacing: 0.5px;
    text-transform: uppercase;
  }
  .wave { position: absolute; left: 0; bottom: 0; width: 100%; display: block; }
  .contact {
    font-family: "Roboto Condensed", Arial, sans-serif;
    font-size: 6.5px;
    color: var(--ink);
    display: flex;
    align-items: center;
    gap: 3px;
    white-space: nowrap;
  }
  .contact svg { width: 6px; height: 6px; flex: none; }

  /* Letterhead */
  .letterhead { left: 32px; top: 28px; width: 347px; height: 450px; }
  .letterhead .wordmark { position: absolute; top: 16px; left: 0; width: 100%; text-align: center; font-size: 17px; }
  .letterhead .wordmark.mark-faint {
    top: 150px; font-size: 58px; color: var(--faint); line-height: 1;
  }
  .letterhead .wave { height: 58px; }
  .letterhead .contact-stack { position: absolute; right: 14px; top: 408px; display: flex; flex-direction: column; align-items: flex-end; gap: 4px; }
  .letterhead .address { position: absolute; left: 16px; top: 432px; }

  /* Fax */
  .fax { left: 417px; top: 28px; width: 347px; height: 450px; }
  .fax .wordmark { position: absolute; top: 16px; left: 28px; font-size: 17px; }
  .fax .contact-stack {
    position: absolute; left: 240px; top: 20px;
    border-left: 1px solid #bbbbbb; padding-left: 5px;
    display: flex; flex-direction: column; gap: 4px;
  }
  .fax h1 { position: absolute; left: 28px; top: 94px; font-size: 22px; font-weight: 400; color: var(--black); }
  .fax .fields { position: absolute; left: 28px; top: 135px; width: 290px; }
  .fax .field-row { display: flex; height: 41px; border-bottom: 1px solid var(--rule); align-items: flex-end; padding-bottom: 6px; }
  .fax .field-row:first-child { height: 23px; }
  .fax .field { font-size: 8.5px; color: var(--black); width: 187px; }
  .fax .field + .field { width: auto; }
  .fax .wave { height: 58px; }
  .fax .address { position: absolute; left: 26px; top: 432px; }
  .fax .wordmark.mark-corner {
    left: auto; right: 14px; top: 414px; font-size: 12px; color: var(--tiffany-soft); text-align: right;
  }

  /* Compliment slips */
  .slip { left: 786px; width: 387px; height: 167px; }
  .slip .band { position: absolute; left: 0; top: 0; width: 100%; height: 58px; display: flex; align-items: center; justify-content: center; }
  .slip .wordmark { font-size: 17px; }
  .slip-white { top: 27px; }
  .slip-white .band { border-bottom: 1px solid #9a9a9a; }
  .slip-black { top: 214px; height: 168px; }
  .slip-black .band { background: var(--black); height: 60px; }
  .slip-black .wordmark { color: var(--white); }
  .slip-tiffany { top: 398px; }
  .slip-tiffany .band { background: var(--tiffany); height: 59px; }
  .slip-tiffany .wordmark { color: var(--white); }

  /* Email signature */
  .signature { left: 28px; top: 530px; width: 367px; height: 100px; }
  .signature .wordmark { position: absolute; left: 10px; top: 8px; font-size: 13px; }
  .signature .person { position: absolute; right: 14px; top: 12px; text-align: right; }
  .signature .person-name { font-size: 9px; font-weight: 500; color: var(--black); letter-spacing: 0.4px; }
  .signature .person-role { font-size: 6.5px; font-weight: 500; color: var(--black); margin-top: 4px; letter-spacing: 0.3px; }
  .signature .contact-line { position: absolute; left: 10px; top: 48px; display: flex; gap: 6px; }
  .signature .web { position: absolute; left: 10px; top: 59px; }
  .signature .wave { height: 40px; }
  .signature .address { position: absolute; right: 14px; top: 84px; }

  /* Envelope */
  .envelope { left: 457px; top: 501px; width: 387px; height: 167px; }
  .envelope .wordmark { position: absolute; left: 20px; top: 15px; font-size: 15px; }
  .envelope .address { position: absolute; left: 16px; top: 66px; }
  .envelope .wave { height: 56px; }
  .envelope .web { position: absolute; left: 14px; top: 151px; font-family: "Roboto Condensed", Arial, sans-serif; font-size: 6px; letter-spacing: 1.2px; color: var(--ink); }
  .envelope .wordmark.mark-corner { left: auto; right: 14px; top: 130px; font-size: 12px; color: var(--tiffany-soft); text-align: right; }
</style>
</head>
<body>

<!-- Letterhead -->
<section class="sheet letterhead" aria-label="Letterhead">
  <div class="wordmark">Campus<br>Northway</div>
  <div class="wordmark mark-faint">Campus<br>Northway</div>
  <svg class="wave" viewBox="0 0 100 30" preserveAspectRatio="none" aria-hidden="true">
    <path d="M0,9 C25,21 55,24 100,4 L100,30 L0,30 Z" fill="var(--tiffany)"/>
    <path d="M0,6.5 C25,18 55,21.5 100,1" fill="none" stroke="var(--black)" stroke-width="2" vector-effect="non-scaling-stroke"/>
    <path d="M0,4 C25,15 55,19 100,-1.5" fill="none" stroke="var(--tiffany)" stroke-width="1" vector-effect="non-scaling-stroke"/>
  </svg>
  <div class="contact-stack">
    <span class="contact"><svg viewBox="0 0 10 10"><path d="M2 1 L4 1 L4.5 3 L3.3 4 Q4.3 6 6 6.7 L7 5.5 L9 6 L9 8 Q5 9 2 5 Q1 3 2 1 Z" fill="var(--ink)"/></svg>+91 20 4471 208</span>
    <span class="contact"><svg viewBox="0 0 10 10"><rect x="3" y="0.5" width="4.5" height="9" rx="0.8" fill="var(--ink)"/></svg>+91 14 3385 617</span>
    <span class="contact"><svg viewBox="0 0 10 10"><circle cx="5" cy="5" r="4.3" fill="var(--ink)"/></svg>www.campusnorthway.com</span>
  </div>
  <span class="contact address"><svg viewBox="0 0 10 10"><path d="M5 1 L9.5 5 L8 5 L8 9 L2 9 L2 5 L0.5 5 Z" fill="var(--ink)"/></svg>Suite B-14 Hill Road</span>
</section>

<!-- Fax cover -->
<section class="sheet fax" aria-label="Fax cover sheet">
  <div class="wordmark">Campus<br>Northway</div>
  <div class="contact-stack">
    <span class="contact"><svg viewBox="0 0 10 10"><path d="M2 1 L4 1 L4.5 3 L3.3 4 Q4.3 6 6 6.7 L7 5.5 L9 6 L9 8 Q5 9 2 5 Q1 3 2 1 Z" fill="var(--ink)"/></svg>+91 20 4471 208</span>
    <span class="contact"><svg viewBox="0 0 10 10"><rect x="3" y="0.5" width="4.5" height="9" rx="0.8" fill="var(--ink)"/></svg>+91 14 3385 617</span>
    <span class="contact"><svg viewBox="0 0 10 10"><circle cx="5" cy="5" r="4.3" fill="var(--ink)"/></svg>www.campusnorthway.com</span>
  </div>
  <h1>FAX</h1>
  <div class="fields">
    <div class="field-row"><span class="field">To</span><span class="field">From</span></div>
    <div class="field-row"><span class="field">Fax</span><span class="field">Pages</span></div>
    <div class="field-row"><span class="field">Phone</span><span class="field">Date</span></div>
    <div class="field-row"><span class="field">Re</span><span class="field">CC</span></div>
  </div>
  <svg class="wave" viewBox="0 0 100 30" preserveAspectRatio="none" aria-hidden="true">
    <path d="M0,9 C25,21 55,24 100,4 L100,30 L0,30 Z" fill="var(--tiffany)"/>
    <path d="M0,6.5 C25,18 55,21.5 100,1" fill="none" stroke="var(--black)" stroke-width="2" vector-effect="non-scaling-stroke"/>
    <path d="M0,4 C25,15 55,19 100,-1.5" fill="none" stroke="var(--tiffany)" stroke-width="1" vector-effect="non-scaling-stroke"/>
  </svg>
  <div class="wordmark mark-corner">Campus<br>Northway</div>
  <span class="contact address"><svg viewBox="0 0 10 10"><path d="M5 1 L9.5 5 L8 5 L8 9 L2 9 L2 5 L0.5 5 Z" fill="var(--ink)"/></svg>Suite B-14 Hill Road</span>
</section>

<!-- Compliment slips -->
<section class="sheet slip slip-white" aria-label="Compliment slip, white">
  <div class="band"><span class="wordmark">Campus Northway</span></div>
</section>
<section class="sheet slip slip-black" aria-label="Compliment slip, black">
  <div class="band"><span class="wordmark">Campus Northway</span></div>
</section>
<section class="sheet slip slip-tiffany" aria-label="Compliment slip, tiffany blue">
  <div class="band"><span class="wordmark">Campus Northway</span></div>
</section>

<!-- Email signature -->
<section class="sheet signature" aria-label="Email signature">
  <div class="wordmark">Campus<br>Northway</div>
  <div class="person">
    <div class="person-name">MR. OWEN CARTER</div>
    <div class="person-role">MARKETING MANAGER</div>
  </div>
  <div class="contact-line">
    <span class="contact"><svg viewBox="0 0 10 10"><path d="M2 1 L4 1 L4.5 3 L3.3 4 Q4.3 6 6 6.7 L7 5.5 L9 6 L9 8 Q5 9 2 5 Q1 3 2 1 Z" fill="var(--ink)"/></svg>+91 20 4471 208</span>
    <span class="contact"><svg viewBox="0 0 10 10"><rect x="3" y="0.5" width="4.5" height="9" rx="0.8" fill="var(--ink)"/></svg>+91 14 3385 617</span>
  </div>
  <span class="contact web"><svg viewBox="0 0 10 10"><circle cx="5" cy="5" r="4.3" fill="var(--ink)"/></svg>www.campusnorthway.com</span>
  <svg class="wave" viewBox="0 0 100 30" preserveAspectRatio="none" aria-hidden="true">
    <path d="M0,10 C25,22 55,23 100,3 L100,30 L0,30 Z" fill="var(--tiffany)"/>
    <path d="M0,7 C25,18 55,20 100,0.8" fill="none" stroke="var(--black)" stroke-width="2" vector-effect="non-scaling-stroke"/>
    <path d="M0,4 C25,15 55,17 100,-1.5" fill="none" stroke="var(--tiffany)" stroke-width="1" vector-effect="non-scaling-stroke"/>
  </svg>
  <span class="contact address"><svg viewBox="0 0 10 10"><path d="M5 1 L9.5 5 L8 5 L8 9 L2 9 L2 5 L0.5 5 Z" fill="var(--ink)"/></svg>Suite B-14 Hill Road</span>
</section>

<!-- Envelope -->
<section class="sheet envelope" aria-label="Envelope">
  <div class="wordmark">Campus<br>Northway</div>
  <span class="contact address">Suite B-14 Hill Road</span>
  <svg class="wave" viewBox="0 0 100 30" preserveAspectRatio="none" aria-hidden="true">
    <path d="M0,7 C20,2 50,5 100,12 L100,30 L0,30 Z" fill="var(--tiffany)"/>
    <path d="M0,4.5 C20,-0.5 50,2.5 100,9.5" fill="none" stroke="var(--black)" stroke-width="2" vector-effect="non-scaling-stroke"/>
    <path d="M0,2 C20,-3 50,0 100,7" fill="none" stroke="var(--tiffany)" stroke-width="1" vector-effect="non-scaling-stroke"/>
  </svg>
  <span class="web">www.campusnorthway.com</span>
  <div class="wordmark mark-corner">Campus<br>Northway</div>
</section>

</body>
</html>
```